Unique Private Wine Label for Wine Bottles (UPDATED BRIEF)

Updated Brief Oct 15, 2017. Please see below!

I am looking for a unique wine label designs for my wine bottles. I create wine and would like to have wine labels for my bottles. I am looking for a main label and then several additional labels with the same design just with the type of wine listed on the label (see below for wine types). This is private wine for family and friends to consume not commercially produced wine.

I would like a rustic, classic or vintage design with some color in the label. I do have a specific name for the wine which i like to call "Thornfield" . I would like to see different designs.

We would like vintage or classic labels. Please give me a few multiple designs based on above. I also want to have a main label and then incorporate different types of wine into the labels like "Chardonnay" or "Pinot Noir" or "Sauvignon Blanc" or "Caberent Savignon" or "Merlot" below the name of the wine. As an example, the labels will be the same design but the word Sauvignon Blanc will be incorporated into the design for this type of wine label and so on for the other types of wine.

Please let me know if you have any questions.
Updates

Project Deadline Extended
Reason: I Have changed the vision of the design. I would like a classic, rustic or vintage design NOT a beach theme. The brief has been updated as of Oct 15, 2017. Please see updated brief for instructions on new design

Note: I have changed the vision of the design. I would like a classic, rustic or vintage design NOT a beach theme. The brief has been updated as of Oct 15, 2017. Please see updated brief for instructions on new design. I would like new designers to provide new designs! Payment is Guaranteed! Thanks!

Target Market(s)

This is private wine for family and friends to consume not commercially produced wine.

Font styles to use
Decorative
Script

Colors

Designer to choose colors to be used in the design.

Requirements
Must have
• Updated Brief Oct 15, 2017. Please see below!
• I am looking for a unique wine label designs for my wine bottles. I create wine and would like to have wine labels for my bottles. I am looking for a main label and then several additional labels with the same design just with the type of wine listed on the label (see below for wine types). This is private wine for family and friends to consume not commercially produced wine.
• I would like a rustic, classic or vintage design with some color in the label. I do have a specific name for the wine which i like to call "Thornfield". I would like to see different designs.
• We would like vintage or classic labels. Please give me a few multiple designs based on above. I also want to have a main label and then incorporate different types of wine into the labels like "Chardonnay" or "Pinot Noir" or "Sauvignon Blanc" or "Caberent Savignon" or "Merlot" below the name of the wine. As an example, the labels will be the same design but the word Sauvignon Blanc will be incorporated into the design for this type of wine label and so on for the other types of wine.
• Please let me know if you have any questions.
Nice to have
Should not have
• Please see the updated brief instructions above. I DO NOT WANT A BEACH THEME ANYMORE!

```html
<!DOCTYPE html>
<html lang="en">
<head>
<meta charset="utf-8">
<title>Thornfield Vineyards – Wine Label</title>
<link href="https://fonts.googleapis.com/css2?family=Playfair+Display:wght@400;700&family=Cormorant+Garamond:ital,wght@1,400&display=swap" rel="stylesheet">
<style>
  :root {
    --backdrop: #7c0000;
    --label-black: #050505;
    --frame-white: #f2f2f2;
    --gold: #e8b94a;
    --gold-light: #f8dc83;
    --gold-deep: #b7831c;
    --cream: #efe6d2;
  }
  html, body {
    margin: 0;
    padding: 0;
    overflow: hidden;
  }
  body {
    width: 846px;
    height: 1200px;
    background: var(--backdrop);
    position: relative;
  }
  .wine-label {
    position: absolute;
    left: 163px;
    top: 220px;
    width: 520px;
    height: 760px;
  }
  .label-frame {
    position: absolute;
    inset: 0;
  }
  .laurel {
    position: absolute;
    left: 150px;
    width: 220px;
    height: 34px;
    background: linear-gradient(90deg, var(--gold-deep), var(--gold-light), var(--gold-deep));
    opacity: 0.85;
  }
  .laurel--top {
    top: 36px;
    border-radius: 110px 110px 0 0 / 34px 34px 0 0;
  }
  .laurel--bottom {
    bottom: 36px;
    border-radius: 0 0 110px 110px / 0 0 34px 34px;
  }
  .vine-emblem {
    position: absolute;
    left: 212px;
    top: 238px;
    width: 96px;
    height: 48px;
    border-radius: 50% 50% 40% 40%;
    background: radial-gradient(circle at 50% 40%, var(--gold-light), var(--gold-deep));
  }
  .grape-cluster {
    position: absolute;
    left: 196px;
    top: 412px;
    width: 128px;
    height: 124px;
    border-radius: 45% 45% 50% 50% / 35% 35% 65% 65%;
    background: radial-gradient(circle at 45% 35%, var(--cream), var(--gold) 80%);
  }
  .brand-name {
    position: absolute;
    left: 0;
    width: 520px;
    text-align: center;
    font-family: "Playfair Display", serif;
    font-weight: 400;
    color: var(--gold);
    font-size: 40px;
    letter-spacing: 1px;
    line-height: 1;
    margin: 0;
  }
  .brand-name--estate { top: 300px; }
  .brand-name--suffix { top: 350px; }
  .tasting-note {
    position: absolute;
    left: 110px;
    top: 578px;
    width: 300px;
    margin: 0;
    text-align: center;
    font-family: "Cormorant Garamond", serif;
    font-style: italic;
    font-size: 13px;
    line-height: 1.35;
    color: var(--frame-white);
  }
  .bottle-details {
    position: absolute;
    left: 0;
    top: 642px;
    width: 520px;
    text-align: center;
    font-family: "Playfair Display", serif;
    font-weight: 700;
    font-size: 15px;
    line-height: 1.25;
    color: var(--frame-white);
    margin: 0;
  }
</style>
</head>
<body>
  <main class="wine-label">
    <svg class="label-frame" width="520" height="760" viewBox="0 0 520 760" aria-hidden="true">
      <defs>
        <path id="star" d="M0,-1 L0.235,-0.324 L0.951,-0.309 L0.38,0.124 L0.588,0.809 L0,0.4 L-0.588,0.809 L-0.38,0.124 L-0.951,-0.309 L-0.235,-0.324 Z"/>
        <linearGradient id="gold-sheen" x1="0" y1="0" x2="1" y2="1">
          <stop offset="0" stop-color="#f8dc83"/>
          <stop offset="1" stop-color="#b7831c"/>
        </linearGradient>
      </defs>
      <path d="M34,0 H486 A34,34 0 0 0 520,34 V726 A34,34 0 0 0 486,760 H34 A34,34 0 0 0 0,726 V34 A34,34 0 0 0 34,0 Z"
            fill="#050505" stroke="#f2f2f2" stroke-width="4"/>
      <path d="M44,12 H476 A32,32 0 0 0 508,44 V716 A32,32 0 0 0 476,748 H44 A32,32 0 0 0 12,716 V44 A32,32 0 0 0 44,12 Z"
            fill="none" stroke="#f2f2f2" stroke-width="1.5"/>
      <g class="star-row" fill="url(#gold-sheen)">
        <use href="#star" transform="translate(168,158) scale(16)"/>
        <use href="#star" transform="translate(208,136) scale(18)"/>
        <use href="#star" transform="translate(260,124) scale(32)"/>
        <use href="#star" transform="translate(312,136) scale(18)"/>
        <use href="#star" transform="translate(352,158) scale(16)"/>
      </g>
      <circle cx="260" cy="380" r="172" fill="none" stroke="#e8b94a" stroke-width="4"/>
      <circle cx="260" cy="380" r="163" fill="none" stroke="#e8b94a" stroke-width="1.5"/>
    </svg>

    <div class="laurel laurel--top" role="img" aria-label="Gold laurel garland arching over the label"></div>
    <div class="vine-emblem" role="img" aria-label="Gold grape bunch with olive sprigs emblem"></div>

    <h1 class="brand-name brand-name--estate">THORNFIELD</h1>
    <p class="brand-name brand-name--suffix">VINEYARDS</p>

    <div class="grape-cluster" role="img" aria-label="Illustration of a gold grape cluster with vine leaves"></div>

    <p class="tasting-note">Crafted slowly from hand picked grapes, aged in oak barrels and shared with family, friends and neighbours around the table each autumn.</p>
    <p class="bottle-details">750ML<br>2017</p>

    <div class="laurel laurel--bottom" role="img" aria-label="Gold laurel garland curving under the label"></div>
  </main>
</body>
</html>
```